Digital Mapping company needs a Proposal Cover Page template (Not Cover Letter).

We are looking for a new design of our proposal's front page. Sales people at Fernrock Surveys will use this new cover page when bidding for jobs, there will be Fernrock Surveys elements that will be set in stone but the potential client information will need to be adaptable/customizable (for example, we currently upload client logos to the home page of our proposals). I attach what we currently have.
Similar look and feel as our tradeshow booth pull up banners and website (www.fernrocksurveys.example) (images of these are also attached). We would like to see designs that use similar colours: green/blue/teal/yellow/orange/red.

We have clients all over the world. We own state of the art mapping equipment (LiDAR). LiDAR and digital photography are acquired with our own Aldwin 418 and other aircraft. The final proposal design should be recognizable and communicate: an experienced company, high quality, and state of the art mapping technology delivered worldwide.

Target Market(s)

Our clients are global and range from small business to large corporations. We have clients associated with Mining, Forestry, Engineering, Ecological and First Nations sectors (usually hired by Geologists & Engineers)

Industry/Entity Type

Technical Service

Font styles to use
Serif

Colors

Designer to choose colors to be used in the design.

Requirements
Must have
• Here are the basic items we would like to see on the cover page of our proposal:
• Our Company Name - Fernrock Surveys Ltd.
• Our Company Logo - attached
• Our Company contact information [customizable field as we have a few locations]
• Proposal service [customizable field to add]
• Proposal project name and location [customizable field to add]
• Proposal Job number [customizable field to add]
• Recipient company or individual and their logo [customizable field’s to add these]
• Date created [auto date]
• Subdued information/less focus on Fernrock Surveys’ name and contact information and a greater focus on the client and their project. Well chosen imagery will tie Fernrock Surveys’ services to the client’s needs without the client thinking about it. Good use of white space as well.
Nice to have
• Similar look and feel as our tradeshow booth pull up banners and website (images of these are attached). We would like to see designs that use similar colours: green/yellow/red/blue/teal.
Should not have
• Something that doesn't match or fit with our logo/website/pull up tradeshow banners that are attached. Something that doesn't include all the elements in our must have list.

```html
<!DOCTYPE html>
<html lang="en">
<head>
<meta charset="utf-8">
<title>Fernrock Surveys – Proposal Template Pages</title>
<link href="https://fonts.googleapis.com/css2?family=Jost:wght@400;500;600;700&display=swap" rel="stylesheet">
<style>
  :root{
    --frame:#f9a958;
    --paper:#ffffff;
    --ink:#111111;
    --navy:#043c6b;
    --royal:#2a3f9e;
    --cyan:#33e3f2;
    --teal:#73d2cf;
    --teal-soft:#c6ecea;
    --teal-pale:#b9e6e6;
    --accent-red:#e3245c;
    --sun:#ffe500;
    --amber:#f6a700;
  }
  *{box-sizing:border-box;margin:0;padding:0}
  html,body{width:927px;height:1200px;overflow:hidden}
  body{background:var(--frame);font-family:"Jost",sans-serif;color:var(--ink);position:relative}
  .page{position:absolute;background:var(--paper);overflow:hidden}
  .page--toc{left:0;top:5px;width:460px;height:555px}
  .page--cover{left:467px;top:5px;width:453px;height:556px}
  .page--scope-a{left:0;top:567px;width:460px;height:626px}
  .page--scope-b{left:467px;top:567px;width:453px;height:626px}

  .contact{position:absolute;font-size:6.4px;line-height:8.4px;font-weight:500;letter-spacing:-.1px;font-style:normal}
  .brand{position:absolute;display:flex;align-items:center;gap:4px;color:var(--navy);font-weight:700;text-transform:uppercase;line-height:1}
  .brand__dot{border-radius:50%;background:var(--navy);flex:none}

  .page-title{position:absolute;font-weight:700;text-transform:uppercase;letter-spacing:.2px}

  /* Table of contents */
  .toc-row{position:absolute;left:50px;width:201px;height:20px}
  .toc-row__mark{position:absolute;left:0;top:0;width:17px;height:17px;background:var(--cyan);transform:rotate(45deg)}
  .toc-row__pin{position:absolute;left:10px;top:15px;width:5px;height:5px;border-radius:50%;background:var(--navy)}
  .toc-row__rule{position:absolute;left:13px;right:0;top:18px;height:1.4px;background:var(--navy)}
  .panel-soft{position:absolute;background:var(--teal-soft)}
  .bracket{position:absolute;border:1.4px solid var(--navy)}

  /* Cover */
  .cover-photo{position:absolute;left:0;top:115px;width:453px;height:352px;
    background:linear-gradient(180deg,#5e5d5a 0%,#6a6152 16%,#c4571b 30%,#d57d17 48%,#c8a61a 64%,#96c21b 84%,#62c51c 100%)}
  .client-logo{position:absolute;left:15px;top:279px;width:74px;height:62px;background:#fff;
    font-size:8.2px;line-height:11.5px;padding:3px 4px;text-transform:uppercase;font-weight:500}
  .cover-title{position:absolute;left:0;top:341px;width:227px;height:173px;background:var(--navy);
    color:#fff;font-size:14.5px;line-height:19px;padding:27px 15px 0;text-transform:uppercase;font-weight:400}
  .cover-title .field{color:var(--accent-red)}
  .rule{position:absolute;height:1.6px;background:var(--navy)}
  .dot{position:absolute;width:5px;height:5px;border-radius:50%;background:var(--navy)}

  /* Scope A */
  .scope-photo{position:absolute;left:155px;top:93px;width:305px;height:164px;
    background:linear-gradient(180deg,#e9eef2 0%,#b7bec6 22%,#4d5a4e 40%,#3f6a35 58%,#7ea54a 78%,#94b85d 100%)}
  .scope-band{position:absolute;left:0;top:306px;width:460px;height:214px;background:var(--royal)}
  .stats{position:absolute;left:144px;top:257px;width:316px;height:98px;background:var(--teal);display:flex;gap:11px;padding:10px 12px 0 12px}
  .stat{width:90px}
  .stat__value{font-size:23px;line-height:24px;font-weight:400}
  .stat__text{font-size:6.6px;line-height:8.2px;margin-top:5px;letter-spacing:-.15px}
  .body-copy{position:absolute;color:#fff;font-size:9.4px;line-height:12px;letter-spacing:-.1px;hyphens:manual}

  /* Scope B */
  .diagram{position:absolute;left:7px;top:138px;width:446px;height:265px;
    background:radial-gradient(ellipse 95px 110px at 122px 122px,#f3c617 0%,#e0b420 45%,rgba(42,63,158,0) 100%),var(--royal)}
  .callout{position:absolute;left:295px;top:370px;width:158px;height:33px;background:var(--teal);
    font-size:20px;font-weight:700;line-height:33px;padding-left:14px}
  .callout-copy{position:absolute;left:91px;top:403px;width:362px;height:148px;background:var(--teal);
    font-size:6.9px;line-height:9px;padding:4px 2px 0 17px;letter-spacing:-.12px}
  .side-block{position:absolute;left:7px;top:420px;width:72px;height:131px;background:var(--teal-pale)}
  .footer-tab{position:absolute;left:0;top:577px;width:81px;height:13px;background:linear-gradient(90deg,var(--teal),#2e8fa8);
    color:#fff;font-size:7px;line-height:13px;padding-left:26px}
  .footer-note{position:absolute;top:578px;font-size:7px;font-weight:600;color:#555}
</style>
</head>
<body>

<section class="page page--toc">
  <address class="contact" style="left:43px;top:39px">
    Fernrock Surveys Ltd.<br>48 Alder Crest Rd.<br>Port Hale BC, V0X 2K1, Canada<br>O. +1(555) 014-2290 | info@fernrocksurveys.example
  </address>
  <div class="brand" style="left:336px;top:44px;font-size:9.5px">
    <span class="brand__dot" style="width:18px;height:18px"></span><span>Fernrock<br>Surveys</span>
  </div>
  <h1 class="page-title" style="left:43px;top:131px;font-size:15px">Table of Contents</h1>

  <div class="toc-row" style="top:188px"><span class="toc-row__mark"></span><span class="toc-row__rule"></span><span class="toc-row__pin"></span></div>
  <div class="toc-row" style="top:232px"><span class="toc-row__mark"></span><span class="toc-row__rule"></span><span class="toc-row__pin"></span></div>
  <div class="toc-row" style="top:276px"><span class="toc-row__mark"></span><span class="toc-row__rule"></span><span class="toc-row__pin"></span></div>
  <div class="toc-row" style="top:320px"><span class="toc-row__mark"></span><span class="toc-row__rule"></span><span class="toc-row__pin"></span></div>
  <div class="toc-row" style="top:364px"><span class="toc-row__mark"></span><span class="toc-row__rule"></span><span class="toc-row__pin"></span></div>
  <div class="toc-row" style="top:408px"><span class="toc-row__mark"></span><span class="toc-row__rule"></span><span class="toc-row__pin"></span></div>
  <div class="toc-row" style="top:452px"><span class="toc-row__mark"></span><span class="toc-row__rule"></span><span class="toc-row__pin"></span></div>
  <div class="toc-row" style="top:496px"><span class="toc-row__mark"></span><span class="toc-row__rule"></span><span class="toc-row__pin"></span></div>

  <div class="panel-soft" style="left:276px;top:163px;width:92px;height:141px"></div>
  <div class="panel-soft" style="left:276px;top:376px;width:92px;height:151px"></div>

  <div class="bracket" style="left:439px;top:158px;width:8px;height:369px;border-right:none;border-radius:4px 0 0 4px"></div>
  <div style="position:absolute;left:449px;top:158px;width:1.6px;height:369px;background:var(--navy)"></div>

  <svg style="position:absolute;left:0;top:373px" width="18" height="36" viewBox="0 0 18 36" aria-hidden="true">
    <polygon points="0,0 18,18 0,36" fill="var(--royal)"/>
  </svg>
</section>

<section class="page page--cover">
  <address class="contact" style="left:26px;top:30px">
    Fernrock Surveys Ltd.<br>48 Alder Crest Rd.<br>Port Hale BC, V0X 2K1, Canada<br>O. +1(555) 014-2290 | info@fernrocksurveys.example
  </address>
  <div class="rule" style="left:315px;top:5px;width:138px;height:2px;background:var(--royal)"></div>
  <div class="brand" style="left:318px;top:18px;font-size:17px">
    <span class="brand__dot" style="width:30px;height:30px"></span><span>Fernrock<br>Surveys</span>
  </div>
  <div class="rule" style="left:310px;top:72px;width:143px;height:2px;background:var(--royal)"></div>

  <svg style="position:absolute;left:0;top:71px" width="62" height="84" viewBox="0 0 62 84" aria-hidden="true">
    <defs><linearGradient id="cornerTop" x1="0" y1="0" x2="1" y2="1"><stop offset="0" stop-color="#33e3f2"/><stop offset="1" stop-color="#2aa6e0"/></linearGradient></defs>
    <polygon points="0,0 62,44 0,84" fill="url(#cornerTop)"/>
    <polygon points="44,32 62,44 48,44" fill="var(--royal)"/>
  </svg>

  <div class="cover-photo" role="img" aria-label="Colour-shaded LiDAR elevation model of mountain peaks, red summits fading to green valleys"></div>

  <svg style="position:absolute;left:351px;top:445px" width="102" height="111" viewBox="0 0 102 111" aria-hidden="true">
    <defs><linearGradient id="cornerBottom" x1="0" y1="0" x2="1" y2="1"><stop offset="0" stop-color="#2aa6e0"/><stop offset="1" stop-color="#33e3f2"/></linearGradient></defs>
    <polygon points="0,25 102,0 102,111" fill="url(#cornerBottom)"/>
    <polygon points="0,25 38,16 44,65" fill="var(--royal)"/>
  </svg>

  <div class="client-logo">[Company logo of who you are sending the proposal]</div>

  <h1 class="cover-title">
    Fernrock Surveys Ltd.<br>Proposal to <span class="field">[Service we are providing]</span> in <span class="field">[Project location]</span> for <span class="field">[Company name].</span><br>
    <span class="field">&nbsp;[Job number]</span>
  </h1>

  <span class="dot" style="left:0;top:528px"></span>
  <div class="rule" style="left:10px;top:530px;width:217px"></div>
  <div class="rule" style="left:10px;top:542px;width:210px"></div>
  <span class="dot" style="left:220px;top:540px"></span>
</section>

<section class="page page--scope-a">
  <div class="contact" style="left:-2px;top:3px">O. +1(555) 014-2290 | info@fernrocksurveys.example</div>
  <div class="brand" style="left:330px;top:-4px;font-size:8px">
    <span class="brand__dot" style="width:12px;height:12px"></span><span>Surveys</span>
  </div>
  <h2 class="page-title" style="left:0;top:79px;font-size:16.5px">Project Scope</h2>

  <div class="panel-soft" style="left:0;top:109px;width:147px;height:197px"></div>
  <div class="scope-photo" role="img" aria-label="Aerial photo of a green river valley below snow-capped mountains"></div>

  <div class="scope-band"></div>
  <div class="stats">
    <div class="stat"><div class="stat__value">10+</div><p class="stat__text">Lorem ipsum dolor sit amet, consectetuer adipiscing elit, sed diam nonummy nibh euismod tincidunt ut laoreet dolore magna aliquam erat volutpat.</p></div>
    <div class="stat"><div class="stat__value">10+</div><p class="stat__text">Lorem ipsum dolor sit amet, consectetuer adipiscing elit, sed diam nonummy nibh euismod tincidunt ut laoreet dolore magna aliquam erat volutpat.</p></div>
    <div class="stat"><div class="stat__value">10+</div><p class="stat__text">Lorem ipsum dolor sit amet, consectetuer adipiscing elit, sed diam nonummy nibh euismod tincidunt ut laoreet dolore magna aliquam erat volutpat.</p></div>
  </div>

  <p class="body-copy" style="left:22px;top:348px;width:172px">Lorem ipsum dolor sit<br>amet, consectetuer adipisc&shy;ing elit, sed diam nonummy nibh euis&shy;mod tincidunt ut laoreet dolore magna aliquam erat volutpat. Ut wisi enim ad minim veniam, quis nostrud exerci tation ullamcorper suscipit lobortis nisl ut aliquip ex ea commodo consequat. Duis autem vel eum iriure dolor in hendrerit in vulputate velit esse molestie conse&shy;quat, vel illum dolore eu feugiat nulla facilisis at vero eros et accumsan et iusto odio dignissim qui blandit praesent</p>
  <p class="body-copy" style="left:257px;top:362px;width:140px">Lorem ipsum dolor sit amet, consectetuer adipiscing elit, sed diam nonummy nibh euismod tincidunt ut laoreet dolore magna aliquam erat volutpat. Ut wisi enim ad minim veniam, quis nostrud exerci tation ullamcorp&shy;er suscipit lobortis nisl ut aliquip ex ea commodo consequat. Duis autem vel eum iriure dolor in hendrerit in vulputate velit esse molestie consequat, vel illum</p>
</section>

<section class="page page--scope-b">
  <address class="contact" style="left:37px;top:7px">
    Fernrock Surveys Ltd.<br>48 Alder Crest Rd.<br>Port Hale BC, V0X 2K1, Canada<br>O. +1(555) 014-2290 | info@fernrocksurveys.example
  </address>
  <div class="brand" style="left:360px;top:12px;font-size:12px">
    <span class="brand__dot" style="width:22px;height:22px"></span><span>Fernrock<br>Surveys</span>
  </div>
  <h2 class="page-title" style="left:37px;top:108px;font-size:16.5px">Project Scope</h2>

  <div class="diagram" role="img" aria-label="Infographic: concentric yellow and orange arcs with six labelled callouts describing project scope items"></div>

  <div class="callout">Place Tex Hre</div>
  <div class="side-block"></div>
  <div class="callout-copy">
    <p>Lorem ipsum dolor sit amet, consectetuer adipiscing elit, sed diam nonummy nibh euismod tincidunt ut laoreet dolore magna aliquam erat volutpat. Ut wisi enim ad minim veniam, quis nostrud exerci tation ullamcorper suscipit lobortis nisl ut aliquip ex ea commodo consequat. Duis autem vel eum iriure dolor in hendrerit in vulputate velit esse molestie consequat, vel illum dolore eu feugiat nulla facilisis at vero eros et accumsan et iusto odio dignissim qui blandit praesent luptatum zzril delenit augue duis dolore te feugait nulla facilisi.</p>
    <p>Lorem ipsum dolor sit amet, cons ectetuer adipiscing elit, sed diam nonummy nibh euismod tincidunt ut laoreet dolore magna aliquam erat volutpat. Ut wisi enim ad minim veniam, quis nostrud exerci tation ullamcorper suscipit lobortis nisl ut aliquip ex ea commodo consequat.</p>
    <p>Lorem ipsum dolor sit amet, consectetuer adipiscing elit, sed diam nonummy nibh euismod tincidunt ut laoreet dolore magna aliquam erat volutpat. Ut wisi enim ad minim veniam, quis nostrud exerci tation ullamcorper suscipit lobortis nisl ut aliquip ex ea commodo consequat. Duis autem vel eum iriure dolor in hendrerit in vulputate velit esse molestie consequat, vel illum dolore eu feugiat nulla facilisis at vero eros et accumsan et iusto odio dignissim qui blandit praesent luptatum zzril delenit augue duis dolore te feugait nulla.</p>
  </div>

  <div class="footer-tab">1 of 13</div>
  <div class="footer-note" style="left:219px">Confidential</div>
  <div class="footer-note" style="left:418px">[Job num</div>
</section>

</body>
</html>
```